Home change of address

Martin & Lena Corwick
WE HAVE MOVED
The address of our new home is
Fern Hollow
48 Bramwell Crescent
Ashby on Wold
Warwickshire
B47 3QT
Tel: 07912 484170
Email: martin@lemar.uk.com

```html
<!DOCTYPE html>
<html lang="en">
<head>
<meta charset="utf-8">
<title>We Have Moved – Martin &amp; Lena Corwick</title>
<link href="https://fonts.googleapis.com/css2?family=Bebas+Neue&family=Barlow+Condensed:wght@300;400;500&family=Questrial&display=swap" rel="stylesheet">
<style>
  :root {
    --green: #2a4d14;
    --orange: #e67f1f;
    --paper: #ffffff;
    --paper-shade: #f3f2f0;
    --band: #e0dfdc;
    --stage: #dcdad5;
    --tree-light: #c9c9c9;
    --tree-dark: #6d6d6d;
  }
  * { margin: 0; padding: 0; box-sizing: border-box; }
  html, body {
    width: 1200px;
    height: 782px;
    overflow: hidden;
    background: var(--stage);
  }
  .announcement {
    position: absolute;
    left: 0;
    top: 93px;
    width: 1200px;
    height: 596px;
    background: var(--paper);
    overflow: hidden;
    color: var(--green);
  }
  .diagonal {
    position: absolute;
    inset: 0;
    width: 1200px;
    height: 596px;
  }
  .names-pill {
    position: absolute;
    left: 84px;
    top: 72px;
    width: 510px;
    height: 81px;
    border: 2px solid var(--green);
    border-radius: 41px;
    display: flex;
    align-items: center;
    justify-content: center;
    font-family: "Bebas Neue", sans-serif;
    font-size: 54px;
    line-height: 1;
    padding-top: 5px;
    letter-spacing: 0.5px;
  }
  .headline {
    position: absolute;
    left: 99px;
    font-family: "Bebas Neue", sans-serif;
    line-height: 1;
  }
  .headline-we-have { top: 174px; font-size: 79px; }
  .headline-moved {
    top: 248px;
    font-size: 126px;
    display: flex;
    align-items: flex-start;
  }
  .moved-o {
    width: 156px;
    height: 88px;
    margin: 8px 10px 0 6px;
    flex: none;
  }
  .intro {
    position: absolute;
    left: 97px;
    top: 392px;
    font-family: "Questrial", sans-serif;
    font-size: 17px;
    font-weight: 700;
    -webkit-text-stroke: 0.3px var(--green);
  }
  .rule {
    position: absolute;
    left: 97px;
    width: 473px;
    height: 1.5px;
    background: var(--green);
  }
  .rule-top { top: 413px; }
  .rule-bottom { top: 475px; }
  .house-name {
    position: absolute;
    left: 94px;
    top: 422px;
    font-family: "Bebas Neue", sans-serif;
    font-size: 50px;
    line-height: 1;
    transform: scaleX(0.82);
    transform-origin: left top;
    font-weight: 400;
  }
  .street-address {
    position: absolute;
    left: 299px;
    top: 427px;
    font-family: "Barlow Condensed", sans-serif;
    font-weight: 500;
    font-size: 17px;
    line-height: 20px;
  }
  .phone {
    position: absolute;
    left: 95px;
    top: 481px;
    font-family: "Barlow Condensed", sans-serif;
    font-weight: 300;
    font-size: 46px;
    line-height: 1;
  }
  .email {
    position: absolute;
    right: 630px;
    top: 497px;
    font-family: "Barlow Condensed", sans-serif;
    font-weight: 400;
    font-size: 19px;
    letter-spacing: 1.6px;
  }
  .divider {
    position: absolute;
    left: 652px;
    top: 43px;
    width: 3px;
    height: 498px;
    background: var(--orange);
  }
  .tree-art {
    position: absolute;
    left: 678px;
    top: 14px;
    width: 522px;
    height: 582px;
    background: radial-gradient(ellipse 60% 45% at 62% 38%, var(--tree-dark) 0%, #9a9a9a 55%, rgba(201,201,201,0.35) 85%, rgba(255,255,255,0) 100%);
  }
</style>
</head>
<body>
  <main class="announcement">
    <svg class="diagonal" viewBox="0 0 1200 596" aria-hidden="true">
      <polygon points="0,119 1200,588 1200,596 0,596" fill="#f3f2f0"/>
      <polygon points="0,119 1200,588 1200,570 0,93" fill="#e0dfdc"/>
    </svg>

    <div class="tree-art" role="img" aria-label="Illustration of a large grey olive tree with a twisted trunk"></div>

    <div class="names-pill">Martin &amp; Lena Corwick</div>

    <h1 class="headline headline-we-have">We Have</h1>
    <div class="headline headline-moved" aria-label="Moved">
      <span>M</span>
      <svg class="moved-o" viewBox="0 0 156 88" aria-hidden="true">
        <rect x="10" y="10" width="136" height="68" rx="34" fill="none" stroke="#e67f1f" stroke-width="20"/>
      </svg>
      <span>VED</span>
    </div>

    <p class="intro">The address of our new home is</p>
    <div class="rule rule-top"></div>
    <p class="house-name">FERN HOLLOW</p>
    <p class="street-address">48 Bramwell Crescent, Ashby on Wold<br>Warwickshire, B47 3QT</p>
    <div class="rule rule-bottom"></div>
    <p class="phone">07912 484170</p>
    <p class="email">martin@lemar.uk.com</p>

    <div class="divider"></div>
  </main>
</body>
</html>
```